Bring me business with this creative business card

Design my new business card. I am looking for something different with an impact. People will take a look at this card & they will 1- see how different & creative I am, 2-understand what I do 3- Call me to meet me!

I make videos with a message, testimonials. I am dynamic, fun, creative & human. My new website is in construction but in the meantime you can check this old one: brightpath.ca & another one Tidebloom.com & tidebloom facebook page.
I make videos. sometimes with a cameraman, sometimes with my phone. As an ex Public Relations agent, the message is the most important thing for me. I want to make my clients shine! When they start with me they often remind me of a lamb, when I finish coaching them they are powerful like LIONS! That's why I need a powerful business card!

Target Market(s)

Entrepreneurs, solo entrepreneurs, small & medium companies & start ups. People i will meet while networking. People that need videos on their website & social Networks to get attention, to be visible. men & women. From 35 to 49 years old.
I am an ex Public relations agent. I used to send clients in traditional medias, now with videos they have more chances to be seen on google the new media. I do videos of the president, his team, his loyal clients saying how great the company is & expert videos like series so people can be seen for example every 1 st of every month with a short 2 minute video. Also with my 20 years in marketing & communications I can coach & give tips to anybody who needs it.
Target: anybody who would like my old website brightpath.ca & I also have another website but it will be off line soon: tidebloom.com could give you ideas.

Industry/Entity Type

Communications

Contact Information for Business Card

I am in Montreal,So the business cards have to be the usual size like we have in Montreal: 9 cm x 5 cm
Details:My text: Mathilde Tessier Communication coach/Lead Storyteller. "Making your message shine on screen" off: 514-555-0147 cell: 514-555-0183. tidebloom.com
mathilde@tidebloom.com logo facebook, youtube, instagram

Colors
f37122

Requirements
Must have
• Dynamic, happy. Orange. Be creative in the look but NOT the shape of the card. Easy to read. Big enough to read.
Should not have
• No funny shapes: no round, no square, just the usual. I love creative but NOT on shape.

```html
<!DOCTYPE html>
<html lang="en">
<head>
<meta charset="utf-8">
<title>Tidebloom business card</title>
<link rel="stylesheet" href="https://fonts.googleapis.com/css2?family=Roboto:wght@400;500;700&display=swap">
<style>
  :root {
    --backdrop: #2b2b2b;
    --paper: #f3f3f3;
    --red-orange: #e8531f;
    --brand-orange: #f37122;
    --amber: #f0a21e;
    --ink: #444444;
    --rule: #9a9a9a;
  }
  * { margin: 0; padding: 0; box-sizing: border-box; }
  html, body { width: 1200px; height: 960px; overflow: hidden; }
  body { background: var(--backdrop); position: relative; font-family: "Roboto", Arial, sans-serif; }

  .card {
    position: absolute;
    left: 312px;
    width: 600px;
    height: 343px;
    background: var(--paper);
  }
  .card--front { top: 113px; }
  .card--back { top: 472px; }

  .mascot-area {
    position: absolute;
    background: radial-gradient(ellipse at 50% 60%, #ffd21a 0%, #f9a316 45%, #f37122 80%, #e8531f 100%);
    border-radius: 30% 30% 45% 45% / 25% 25% 55% 55%;
  }
  .card--front .mascot-area { left: 450px; top: 35px; width: 110px; height: 135px; }
  .card--back .mascot-area { left: 249px; top: 61px; width: 102px; height: 127px; }

  .person-name {
    position: absolute; left: 48px; top: 186px;
    font-weight: 500; font-size: 23px; letter-spacing: 0.2px;
    color: var(--red-orange);
  }
  .person-role {
    position: absolute; left: 48px; top: 213px;
    font-weight: 500; font-size: 15px; line-height: 20px;
    color: var(--amber);
  }
  .contact {
    position: absolute; top: 264px;
    font-size: 14px; line-height: 19px; color: var(--ink);
  }
  .contact--phones { left: 50px; }
  .contact--online { left: 203px; }
  .contact-row { display: flex; align-items: center; height: 19px; }
  .contact-row svg { width: 13px; height: 13px; margin-right: 9px; flex: none; }
  .contact-divider {
    position: absolute; left: 185px; top: 265px;
    width: 1px; height: 36px; background: var(--rule);
  }

  .wordmark {
    position: absolute; left: 0; width: 100%; top: 197px;
    text-align: center;
    font-weight: 500;
    font-size: 31px; letter-spacing: 2px; line-height: 38px;
    color: var(--brand-orange);
  }
  .tagline {
    position: absolute; left: 0; width: 100%; top: 237px;
    display: flex; justify-content: center; align-items: center; gap: 6px;
    font-size: 13px; letter-spacing: 0.4px; color: var(--brand-orange);
  }
  .tagline::before, .tagline::after {
    content: ""; width: 32px; height: 1px; background: var(--amber);
  }
  .slogan {
    position: absolute; left: 0; width: 100%; top: 255px;
    text-align: center;
    font-weight: 500; font-size: 14px; color: var(--red-orange);
  }
  .social-row {
    position: absolute; left: 168px; top: 297px;
    width: 264px; height: 22px;
    display: flex; align-items: center; gap: 5px;
  }
  .social-row .rule {
    flex: 1; height: 1px;
    background: linear-gradient(to right, transparent, var(--red-orange));
  }
  .social-row .rule--right {
    background: linear-gradient(to left, transparent, var(--red-orange));
  }
  .social-dot {
    width: 22px; height: 22px; border-radius: 50%;
    background: var(--red-orange);
  }
</style>
</head>
<body>

<section class="card card--front">
  <div class="mascot-area" role="img" aria-label="Low-poly orange animal head illustration"></div>

  <div class="person-name">MATHILDE T.</div>
  <div class="person-role">COMMUNICATION COACH<br>LEAD STORYTELLER</div>

  <div class="contact contact--phones">
    <div class="contact-row">
      <svg viewBox="0 0 16 16" aria-hidden="true"><path fill="#e8531f" d="M3.6 1.2l2.3 2.6-1.3 2a9 9 0 0 0 5.6 5.6l2-1.3 2.6 2.3-1.5 2.1C7.8 16.2-.2 8.2.7 2.7z"/></svg>
      <span>514-555-0147</span>
    </div>
    <div class="contact-row">
      <svg viewBox="0 0 16 16" aria-hidden="true"><rect x="4" y="0.5" width="8" height="15" rx="1.5" fill="#e8531f"/><rect x="5.5" y="2.5" width="5" height="9" fill="#f3f3f3"/></svg>
      <span>514-555-0183</span>
    </div>
  </div>
  <div class="contact-divider"></div>
  <div class="contact contact--online">
    <div class="contact-row">
      <svg viewBox="0 0 16 16" aria-hidden="true"><rect x="1" y="3.5" width="14" height="10" fill="#e8531f"/><path d="M1 4l7 5 7-5" fill="none" stroke="#f3f3f3" stroke-width="1.3"/></svg>
      <span>mathilde@tidebloom.com</span>
    </div>
    <div class="contact-row">
      <svg viewBox="0 0 16 16" aria-hidden="true"><circle cx="8" cy="8" r="7" fill="#e8531f"/><path d="M4 5c2 0 2 2 4 2s1 3 3 3M9 3c0 2 2 2 3 3" fill="none" stroke="#f3f3f3" stroke-width="1.2"/></svg>
      <span>www.tidebloom.com</span>
    </div>
  </div>
</section>

<section class="card card--back">
  <div class="mascot-area" role="img" aria-label="Low-poly orange animal head illustration"></div>
  <div class="wordmark">TIDEBLOOM</div>
  <div class="tagline">ONE STORY ONE VOICE</div>
  <div class="slogan">Making your message shine on screen</div>
  <div class="social-row">
    <span class="rule"></span>
    <span class="social-dot"></span>
    <span class="social-dot"></span>
    <span class="social-dot"></span>
    <span class="rule rule--right"></span>
  </div>
</section>

</body>
</html>
```